MRT Property - Business Cards

Looking for a business card & general letterhead, signage etc design for our new logo.

Colours:
000a20
0056a2
00b5ef
0088ce
68cef2

Fonts:
Poppins
Karla

Please keep look and feel of new brand - example in the zip package I sent.

```html
<!DOCTYPE html>
<html lang="en">
<head>
<meta charset="utf-8">
<title>MRT Property – Business Card</title>
<link rel="stylesheet" href="https://fonts.googleapis.com/css2?family=Poppins:wght@400;700&display=swap">
<style>
  :root {
    --ink: #000a20;
    --navy: #0a3f7f;
    --brand-blue: #0056a2;
    --mid-blue: #0088ce;
    --cyan: #00b5ef;
    --sky: #68cef2;
    --card-face: #eef1f4;
    --page: #d9dde2;
    --contact-text: #dbe6f2;
  }
  html, body {
    margin: 0;
    width: 1200px;
    height: 887px;
    overflow: hidden;
    background: var(--page);
  }
  .business-card {
    position: absolute;
    left: 80px;
    top: 157px;
    width: 1040px;
    height: 573px;
    border-radius: 26px;
    overflow: hidden;
    background: var(--card-face);
    box-shadow: 0 10px 30px rgba(0, 10, 32, 0.18);
  }
  .business-card svg {
    display: block;
    width: 100%;
    height: 100%;
  }
  .brand-name {
    font-family: "Poppins", sans-serif;
    font-weight: 700;
    fill: var(--brand-blue);
  }
  .person-first { font-family: "Poppins", sans-serif; font-weight: 700; fill: var(--navy); }
  .person-last { font-family: "Poppins", sans-serif; font-weight: 700; fill: var(--brand-blue); }
  .person-title { font-family: "Poppins", sans-serif; font-weight: 400; fill: var(--ink); }
  .contact-line {
    font-family: "Poppins", sans-serif;
    font-weight: 400;
    fill: var(--contact-text);
  }
  .contact-icon { fill: none; stroke: var(--sky); stroke-width: 1.6; }
</style>
</head>
<body>
  <div class="business-card">
    <svg viewBox="0 0 980 538" preserveAspectRatio="none" xmlns="http://www.w3.org/2000/svg">
      <defs>
        <linearGradient id="band-fill" x1="0" y1="0" x2="0" y2="1">
          <stop offset="0" stop-color="#0a6cc0"/>
          <stop offset="1" stop-color="#0a3f8f"/>
        </linearGradient>
      </defs>

      <!-- brand name -->
      <g class="brand-lockup">
        <circle cx="80" cy="112" r="24" fill="var(--cyan)"/>
        <text class="brand-name" x="118" y="132" font-size="54">MRT Property</text>
      </g>

      <!-- person -->
      <text class="person-first" x="927" y="88" font-size="40" text-anchor="end">DANA <tspan class="person-last">WHITFIELD</tspan></text>
      <text class="person-title" x="927" y="116" font-size="21" text-anchor="end">Founder &amp; Principal</text>
      <rect class="name-bar" x="963" y="57" width="17" height="60" fill="var(--brand-blue)"/>

      <!-- decorative band area -->
      <rect class="decor-band" x="0" y="285" width="980" height="253" fill="url(#band-fill)" role="img" aria-label="Decorative blue wave artwork"/>

      <!-- contact -->
      <g class="contact-block" font-size="21">
        <text class="contact-line" x="900" y="321" text-anchor="end">+1- 555-014-2093</text>
        <text class="contact-line" x="900" y="351" text-anchor="end">info@mrtproperty.com</text>
        <text class="contact-line" x="900" y="381" text-anchor="end">www.mrtproperty.com</text>
        <text class="contact-line" x="927" y="438" text-anchor="end">4120 North Maple Avenue</text>
        <text class="contact-line" x="927" y="468" text-anchor="end">#18, Suite Riverton</text>
      </g>
      <g class="contact-icons">
        <path class="contact-icon" d="M912,306 l4,0 l2,5 l-3,2 q2,4 6,6 l2,-3 l5,2 l0,4 q-10,1 -16,-16 z"/>
        <rect class="contact-icon" x="910" y="338" width="17" height="11" rx="1"/>
        <path class="contact-icon" d="M910,339 l8.5,6 l8.5,-6"/>
        <circle class="contact-icon" cx="918.5" cy="374" r="8"/>
        <path class="contact-icon" d="M910.5,374 h16 M918.5,366 q-5,8 0,16 q5,-8 0,-16"/>
      </g>
    </svg>
  </div>
</body>
</html>
```